Animal Eye Clinic needs a Business card

We are a new veterinary ophthalmology practice (Ridgeline Pet Vision Care) and we need a business card designed. We only see animal eyes - we are not a regular veterinary clinic. We already have a logo. We are looking for a professional, good looking business card to hand out to our clients. We are looking for something simple but professional and contemporary. Our logo is likely the only picture/graphic that needs to be on the card.
Updates

Contact Information for Business Card

Delia Vossman, BSc, DVM, MSc, DipACVO
Veterinary Ophthalmologist

Phone: 250.418.3927
Email: ridgelinepetvisioncare@mailbox-example.net
Website: ridgelinepetvisioncare-example.net
Address: 1874 Thornbury Rd
Kelowna, BC, V1X 4M9

Colors

Designer to choose colors to be used in the design.

Requirements
Must have
• Our logo (attached)

```html
<!DOCTYPE html>
<html lang="en">
<head>
<meta charset="utf-8">
<title>Ridgeline Pet Vision Care – Business Card</title>
<link rel="stylesheet" href="https://fonts.googleapis.com/css2?family=Montserrat:wght@400;700&family=Quicksand:wght@400;500&display=swap">
<style>
  :root {
    --teal: #1a96a8;
    --slate: #717171;
    --ink: #6a6a6a;
    --paper: #ffffff;
    --backdrop: #e9e9e7;
  }
  * { box-sizing: border-box; margin: 0; padding: 0; }
  html, body { width: 1200px; height: 900px; overflow: hidden; }
  body {
    background: var(--backdrop);
    position: relative;
    font-family: "Quicksand", sans-serif;
  }
  .card {
    position: absolute;
    left: 250px;
    width: 700px;
    height: 400px;
    overflow: hidden;
    box-shadow: 0 6px 18px rgba(0,0,0,0.12);
  }
  .card--front { top: 40px; background: var(--paper); }
  .card--back { top: 470px; background: var(--slate); }

  .front-arcs { position: absolute; inset: 0; }

  .brand-mark {
    position: absolute;
    left: 28px;
    top: 150px;
    width: 200px;
    display: flex;
    align-items: center;
    gap: 10px;
  }
  .brand-mark__dot {
    flex: none;
    width: 22px; height: 22px;
    border-radius: 50%;
    background: var(--teal);
  }
  .brand-mark__name {
    font-family: "Montserrat", sans-serif;
    font-weight: 700;
    font-size: 17px;
    line-height: 1.25;
    color: var(--teal);
    text-transform: uppercase;
    letter-spacing: 1px;
  }

  .identity { position: absolute; left: 370px; top: 52px; }
  .identity__name {
    font-family: "Montserrat", sans-serif;
    font-size: 29px;
    letter-spacing: 4px;
    text-transform: uppercase;
    line-height: 1;
    white-space: nowrap;
  }
  .identity__first { color: var(--teal); font-weight: 700; }
  .identity__last { color: var(--ink); font-weight: 400; }
  .identity__role,
  .identity__creds {
    font-family: "Montserrat", sans-serif;
    font-size: 13px;
    color: var(--ink);
    letter-spacing: 0.5px;
    text-transform: uppercase;
    margin-top: 6px;
  }
  .identity__creds {
    display: inline-block;
    margin-top: 3px;
    padding-bottom: 5px;
    border-bottom: 2px solid var(--teal);
    padding-right: 70px;
  }

  .contacts {
    position: absolute;
    left: 370px;
    top: 190px;
    list-style: none;
  }
  .contacts__item {
    display: flex;
    align-items: center;
    gap: 12px;
    height: 36px;
    font-size: 11.5px;
    font-weight: 500;
    letter-spacing: 0.6px;
    color: var(--ink);
    white-space: nowrap;
  }
  .contacts__icon {
    flex: none;
    width: 22px; height: 22px;
    border-radius: 5px;
    background: var(--teal);
    display: flex; align-items: center; justify-content: center;
  }
  .contacts__icon svg { width: 13px; height: 13px; }

  .back-brand {
    position: absolute;
    left: 0; right: 0; top: 135px;
    display: flex;
    align-items: center;
    justify-content: center;
    gap: 18px;
  }
  .back-brand__dot {
    width: 56px; height: 56px;
    border-radius: 50%;
    background: var(--paper);
  }
  .back-brand__name {
    font-family: "Montserrat", sans-serif;
    font-weight: 700;
    font-size: 30px;
    line-height: 1.15;
    letter-spacing: 2px;
    text-transform: uppercase;
    color: var(--paper);
  }
  .back-site {
    position: absolute;
    left: 0; right: 0; bottom: 52px;
    text-align: center;
    font-size: 19px;
    letter-spacing: 3px;
    color: var(--paper);
  }
</style>
</head>
<body>

<section class="card card--front" aria-label="Business card front">
  <svg class="front-arcs" viewBox="0 0 700 400" aria-hidden="true">
    <circle cx="10" cy="250" r="335" fill="var(--slate)"/>
    <circle cx="-10" cy="190" r="320" fill="var(--teal)"/>
    <circle cx="-20" cy="205" r="300" fill="var(--paper)"/>
  </svg>

  <div class="brand-mark">
    <span class="brand-mark__dot"></span>
    <span class="brand-mark__name">Ridgeline Pet<br>Vision Care</span>
  </div>

  <div class="identity">
    <h1 class="identity__name"><span class="identity__first">Delia</span> <span class="identity__last">Vossman</span></h1>
    <p class="identity__role">Veterinary Ophthalmologist</p>
    <p class="identity__creds">BSc, DVM, MSc, DipACVO</p>
  </div>

  <ul class="contacts">
    <li class="contacts__item">
      <span class="contacts__icon">
        <svg viewBox="0 0 24 24"><path fill="#fff" d="M6.6 10.8a15.2 15.2 0 0 0 6.6 6.6l2.2-2.2c.3-.3.7-.4 1-.2 1.1.4 2.3.6 3.6.6.6 0 1 .4 1 1V20c0 .6-.4 1-1 1A17 17 0 0 1 3 4c0-.6.4-1 1-1h3.5c.6 0 1 .4 1 1 0 1.3.2 2.5.6 3.6.1.3 0 .7-.2 1z"/></svg>
      </span>
      250.418.3927
    </li>
    <li class="contacts__item">
      <span class="contacts__icon">
        <svg viewBox="0 0 24 24"><path fill="#fff" d="M12 2a7 7 0 0 0-7 7c0 5.2 7 13 7 13s7-7.8 7-13a7 7 0 0 0-7-7zm0 9.5A2.5 2.5 0 1 1 12 6.5a2.5 2.5 0 0 1 0 5z"/></svg>
      </span>
      1874 Thornbury Rd Kelowna, BC, V1X 4M9
    </li>
    <li class="contacts__item">
      <span class="contacts__icon">
        <svg viewBox="0 0 24 24"><path fill="#fff" d="M3 5h18v14H3z"/><path fill="none" stroke="var(--teal)" stroke-width="2" d="M3.5 6l8.5 7 8.5-7"/></svg>
      </span>
      ridgelinepetvisioncare@mailbox-example.net
    </li>
    <li class="contacts__item">
      <span class="contacts__icon">
        <svg viewBox="0 0 24 24"><g fill="none" stroke="#fff" stroke-width="2"><circle cx="12" cy="12" r="9"/><path d="M3 12h18M12 3c3 3 3 15 0 18M12 3c-3 3-3 15 0 18"/></g></svg>
      </span>
      ridgelinepetvisioncare-example.net
    </li>
  </ul>
</section>

<section class="card card--back" aria-label="Business card back">
  <div class="back-brand">
    <span class="back-brand__dot"></span>
    <span class="back-brand__name">Ridgeline Pet<br>Vision Care</span>
  </div>
  <p class="back-site">ridgelinepetvisioncare-example.net</p>
</section>

</body>
</html>
```